Need help in designing new business card utilizing our new logo.

BuildMark Solutions works with Construction Business Owners, Managers & IT Professionals to strengthen software usage and increase user productivity.

Our Construction Accounting and Mobile Field Management Software Clients engage with us in the following areas:

New Software Implementations
Software Re-Implementations
Redesigning Software Usage at the User Level
Project Coordination & Management
Continued Software Support

Old tag line:
Weighing Options - Implementing Solutions

www.buildmark-solutions.example

Ridge 4 is a product, but not needed for a new business card.

```html
<!DOCTYPE html>
<html lang="en">
<head>
<meta charset="utf-8">
<title>BuildMark Solutions – Business Card</title>
<link href="https://fonts.googleapis.com/css2?family=Roboto:wght@300;400;500;700&display=swap" rel="stylesheet">
<style>
  :root {
    --page: #5a5b5e;
    --card: #222326;
    --card-edge: #2b2c30;
    --blue: #0f4fa3;
    --blue-bright: #1f5fb8;
    --silver: #b9bbbf;
    --white: #f2f3f5;
    --muted: #8d8f94;
  }
  * { box-sizing: border-box; margin: 0; padding: 0; }
  html, body { width: 799px; height: 1200px; overflow: hidden; }
  body {
    background: var(--page);
    font-family: "Roboto", Arial, sans-serif;
    color: var(--white);
    position: relative;
  }
  .card {
    position: absolute;
    left: 90px;
    width: 620px;
    height: 354px;
    background: var(--card);
    border-radius: 22px;
    overflow: hidden;
    box-shadow: 0 14px 30px rgba(0,0,0,.45);
  }
  .card--front { top: 110px; }
  .card--back { top: 736px; }

  /* brand lockup */
  .brand {
    display: flex;
    align-items: center;
    gap: 14px;
    font-weight: 500;
  }
  .brand__mark { width: 40px; height: 40px; }
  .brand__name { font-size: 30px; letter-spacing: .5px; }

  /* front */
  .card--front .brand {
    position: absolute;
    top: 44px;
    left: 0; right: 0;
    justify-content: center;
    color: var(--silver);
  }
  .card--front .brand__mark { background: #141518; }
  .services {
    position: absolute;
    top: 128px;
    left: 0; right: 0;
    height: 118px;
    background: var(--blue);
    display: flex;
    flex-direction: column;
    justify-content: center;
    align-items: center;
    gap: 6px;
    font-size: 17px;
    font-weight: 400;
  }
  .services__sep { margin: 0 10px; }
  .website {
    position: absolute;
    top: 272px;
    left: 0; right: 0;
    display: flex;
    align-items: center;
    justify-content: center;
    gap: 26px;
    font-size: 16px;
  }
  .website__rule { width: 44px; height: 2px; background: var(--muted); border-radius: 1px; }

  /* back */
  .tagline-strip {
    position: absolute;
    left: 0; top: 0; bottom: 0;
    width: 52px;
    background: var(--blue);
    border-right: 8px solid #c8cace;
  }
  .tagline {
    position: absolute;
    left: 22px;
    top: 50%;
    transform: translate(-50%, -50%) rotate(-90deg);
    white-space: nowrap;
    font-size: 14px;
  }
  .card--back .brand {
    position: absolute;
    top: 40px;
    left: 96px;
    color: var(--blue-bright);
  }
  .card--back .brand__mark { background: var(--blue-bright); }
  .person { position: absolute; top: 106px; left: 96px; }
  .person__name { font-size: 24px; font-weight: 700; color: var(--blue-bright); }
  .person__role { font-size: 13px; margin-top: 4px; }
  .contacts { position: absolute; top: 172px; left: 96px; list-style: none; }
  .contacts li {
    display: flex;
    align-items: center;
    gap: 12px;
    font-size: 15px;
    line-height: 24px;
  }
  .contacts svg { width: 13px; height: 13px; fill: var(--muted); flex: none; }
  .address { position: absolute; top: 300px; left: 96px; font-size: 15px; }
</style>
</head>
<body>

<section class="card card--front" aria-label="Card front">
  <div class="brand">
    <span class="brand__mark"></span>
    <span class="brand__name">BuildMark Solutions</span>
  </div>
  <div class="services">
    <p>New Software Implementations<span class="services__sep">|</span>Software Re-Implementations</p>
    <p>Redesigning Software Usage at the User Level</p>
    <p>Project Coordination &amp; Management<span class="services__sep">|</span>Continued Software Support</p>
  </div>
  <div class="website">
    <span class="website__rule"></span>
    <span>www.buildmark-solutions.example</span>
    <span class="website__rule"></span>
  </div>
</section>

<section class="card card--back" aria-label="Card back">
  <div class="tagline-strip">
    <p class="tagline">Weighing Options - Implementing Solutions</p>
  </div>
  <div class="brand">
    <span class="brand__mark"></span>
    <span class="brand__name">BuildMark Solutions</span>
  </div>
  <div class="person">
    <p class="person__name">Dana R. Whitfield</p>
    <p class="person__role">Owner</p>
  </div>
  <ul class="contacts">
    <li>
      <svg viewBox="0 0 16 16" aria-hidden="true"><rect x="4" y="1" width="8" height="14" rx="1.5"/></svg>
      555-014-7567
    </li>
    <li>
      <svg viewBox="0 0 16 16" aria-hidden="true"><path d="M3 1l3 3-2 2c1 2 3 4 5 5l2-2 3 3-2 3C7 14 2 9 1 3z"/></svg>
      555-019-6650 ext. 100
    </li>
    <li>
      <svg viewBox="0 0 16 16" aria-hidden="true"><path d="M1 3h14v10H1z M1 3l7 6 7-6" /></svg>
      dana.whitfield@buildmark-solutions.example
    </li>
    <li>
      <svg viewBox="0 0 16 16" aria-hidden="true"><circle cx="8" cy="8" r="7"/></svg>
      www.buildmark-solutions.example
    </li>
  </ul>
  <p class="address">48B Harbor Lane - PMB 112 Millbrook, NY 10000</p>
</section>

</body>
</html>
```